Ward Compass Business Card Design*

We need a business card design for our company Ward Compass. Our company is specialized in providing online consulting services regarding medical institutions, hospitals and doctors. We work with patients worldwide looking to choose between healthcare providers. We have a website you may use as a reference, where we list doctors and clinics worldwide. So we target Medical providers as well as patients worldwide.
Target Market(s)
Medical Providers and patients around the world
Industry/Entity Type
Medical
Contact Information for Business Card
Salwa Kettani
CEO
+90 612 348 2175
info@wardcompass.example
www.wardcompass.example
14 Annakhil 7 H.R.B. Rabat, Morocco
Requirements
Must have
- Company logo/name on one full side, personal info and smaller logo and company name on the other side.
Nice to have
- Smart and elegant design

```html
<!DOCTYPE html>
<html lang="en">
<head>
<meta charset="utf-8">
<title>Ward Compass – Business Card</title>
<link rel="stylesheet" href="https://fonts.googleapis.com/css2?family=Montserrat:wght@600&family=Roboto:wght@400;500;700&display=swap">
<style>
  :root {
    --navy: #143864;
    --white: #ffffff;
    --grey-light: #a3a3a3;
    --grey-mid: #939393;
    --grey-dark: #818181;
    --stage: #2c2f35;
  }
  * { margin: 0; padding: 0; box-sizing: border-box; }
  html, body { width: 1200px; height: 1000px; overflow: hidden; }
  body {
    background: var(--stage);
    font-family: "Roboto", Arial, sans-serif;
    position: relative;
  }
  .card {
    position: absolute;
    left: 250px;
    width: 700px;
    height: 400px;
    border-radius: 22px;
    overflow: hidden;
    box-shadow: 0 12px 30px rgba(0,0,0,.45);
  }
  .card--back { top: 55px; background: var(--navy); display: flex; align-items: center; justify-content: center; }
  .card--front { top: 540px; background: var(--navy); }

  .brand-name {
    font-family: "Montserrat", Arial, sans-serif;
    font-weight: 600;
    letter-spacing: .04em;
    text-transform: uppercase;
    white-space: nowrap;
  }
  .card--back .brand-name { color: var(--white); font-size: 42px; }

  .front-shape { position: absolute; inset: 0; width: 100%; height: 100%; }

  .front-brand {
    position: absolute;
    left: 50px;
    top: 178px;
    display: flex;
    align-items: center;
    gap: 14px;
  }
  .front-brand .brand-dot { width: 26px; height: 26px; border-radius: 50%; background: var(--navy); }
  .front-brand .brand-name { color: var(--navy); font-size: 26px; }

  .contact {
    position: absolute;
    left: 410px;
    top: 82px;
    color: var(--white);
  }
  .contact__name { font-weight: 700; font-size: 24px; letter-spacing: .02em; text-transform: uppercase; }
  .contact__role { font-weight: 500; font-size: 18px; margin-top: 4px; }
  .contact__rule { width: 38px; height: 3px; background: var(--white); margin-top: 8px; }
  .contact__address { font-size: 16px; line-height: 1.3; margin-top: 28px; }
  .contact__list { list-style: none; margin-top: 12px; }
  .contact__list li { display: flex; align-items: center; gap: 10px; font-size: 16px; line-height: 1.75; }
  .contact__list svg { width: 13px; height: 13px; flex: none; }
</style>
</head>
<body>

<section class="card card--back" aria-label="Card back">
  <span class="brand-name">Ward Compass</span>
</section>

<section class="card card--front" aria-label="Card front">
  <svg class="front-shape" viewBox="0 0 700 400" aria-hidden="true">
    <circle cx="-150" cy="170" r="535" fill="var(--grey-dark)"/>
    <circle cx="-150" cy="170" r="520" fill="var(--grey-mid)"/>
    <circle cx="-150" cy="170" r="505" fill="var(--grey-light)"/>
    <circle cx="-150" cy="170" r="490" fill="var(--white)"/>
  </svg>

  <div class="front-brand">
    <span class="brand-dot"></span>
    <span class="brand-name">Ward Compass</span>
  </div>

  <div class="contact">
    <p class="contact__name">Salwa Kettani</p>
    <p class="contact__role">CEO</p>
    <div class="contact__rule"></div>
    <p class="contact__address">14 Annakhil 7 H.R.B.<br>Rabat, Morocco</p>
    <ul class="contact__list">
      <li>
        <svg viewBox="0 0 24 24" fill="var(--white)"><path d="M6.6 10.8a15.1 15.1 0 0 0 6.6 6.6l2.2-2.2a1 1 0 0 1 1-.25 11.4 11.4 0 0 0 3.6.57 1 1 0 0 1 1 1V20a1 1 0 0 1-1 1A17 17 0 0 1 3 4a1 1 0 0 1 1-1h3.5a1 1 0 0 1 1 1c0 1.25.2 2.45.57 3.57a1 1 0 0 1-.25 1z"/></svg>
        +90 612 348 2175
      </li>
      <li>
        <svg viewBox="0 0 24 24" fill="none" stroke="var(--white)" stroke-width="2.4"><rect x="2" y="5" width="20" height="14" rx="1"/><path d="M2 6l10 7 10-7"/></svg>
        info@wardcompass.example
      </li>
      <li>
        <svg viewBox="0 0 24 24" fill="none" stroke="var(--white)" stroke-width="2"><circle cx="12" cy="12" r="10"/><path d="M2 12h20M12 2a15 15 0 0 1 0 20M12 2a15 15 0 0 0 0 20"/></svg>
        www.wardcompass.example
      </li>
    </ul>
  </div>
</section>

</body>
</html>
```